Dental Practice Billboard Design

We are a newer dental practice in need of a simple but appealing billboard for our growing dental practice to attract new patients. The practice is owned by husband and wife dentists and is family friendly in a small town in Kentucky. We try to be very friendly and caring to our patients. Would prefer a blue background for the billboard and our tooth logo to be prominent. We are partial to the Patua One font used in the image below but please feel free to tweak it as you deem necessary. The shape of the uppercase D and lowercase g are why we like that font, so fonts with a similarly shaped “D” and “g” would work as well. Please include our phone number (555) 847-1390. Please see our website Harlowbrookdentistry.example for more info on the practice if needed. Thank you! Looking forward to seeing your creation.
Updates

The dimensions will be 12ft x 24ft (3.6576m x 7.3152m). Apologies for not including this in the original prompt. Thank you all for your submissions.

Industry/Entity Type

Dental

Font styles to use
Other font styles liked:
• Patua One

Colors
0054AA
0677BA
7BADD7
CADEEF
E8F1F8
0094D4
00A9DD
6FCCEA
C7EBF8
E9F6FB
00AB8E
00BBA5
67D7C9
C6EFE9
E9F9F6
59FF00
82FF00
B8FF75
E3FFCB
F4FFEA

Requirements
Must have
• Phone number, website, Logo, Practice name “Harlow Brook Dentistry”
Should not have
• A tagline or slogan

```html
<!DOCTYPE html>
<html lang="en">
<head>
<meta charset="utf-8">
<title>Harlow Brook Dentistry Billboard</title>
<link rel="stylesheet" href="https://fonts.googleapis.com/css2?family=Patua+One&family=Fira+Sans+Condensed:wght@600&display=swap">
<style>
  :root {
    --navy: #1b2a55;
    --green: #2bb24c;
    --white: #ffffff;
    --page: #ffffff;
    --smile-light: #f7e6e3;
    --smile-mid: #d98a8e;
  }
  * { margin: 0; padding: 0; box-sizing: border-box; }
  html, body { width: 992px; height: 1200px; overflow: hidden; background: var(--page); }
  .canvas { position: relative; width: 992px; height: 1200px; }

  .billboard {
    position: absolute; left: 0; top: 0;
    width: 992px; height: 517px;
    background: var(--navy);
    overflow: hidden;
  }
  .burst { position: absolute; left: 0; top: 0; width: 992px; height: 517px; }

  .brand-mark {
    position: absolute; left: 82px; top: 62px;
    width: 146px; height: 146px; border-radius: 50%;
    background: var(--green);
  }
  .brand-name {
    position: absolute; left: 246px; top: 74px;
    font-family: "Patua One", Georgia, serif;
    font-weight: 400; color: var(--white);
    white-space: nowrap;
  }
  .brand-name__primary { display: block; font-size: 54px; line-height: 66px; }
  .brand-name__secondary { display: block; font-size: 54px; line-height: 62px; }

  .website {
    position: absolute; left: 106px; top: 264px;
    font-family: "Patua One", Georgia, serif;
    font-size: 31px; line-height: 40px;
    color: var(--white); white-space: nowrap;
  }
  .phone-pill {
    position: absolute; left: 101px; top: 351px;
    width: 613px; height: 105px; border-radius: 53px;
    background: var(--green);
    display: flex; align-items: center;
    padding-left: 50px; gap: 14px;
  }
  .phone-icon { width: 44px; height: 64px; flex: none; }
  .phone-number {
    font-family: "Fira Sans Condensed", "Arial Narrow", sans-serif;
    font-weight: 600; font-size: 76px; line-height: 1;
    color: var(--white); letter-spacing: -0.5px;
    white-space: nowrap;
  }
</style>
</head>
<body>
<main class="canvas">
  <section class="billboard">
    <svg class="burst" viewBox="0 0 992 517">
      <defs>
        <linearGradient id="smileFill" x1="0" y1="0" x2="0" y2="1">
          <stop offset="0" stop-color="var(--smile-mid)"/>
          <stop offset="0.5" stop-color="var(--smile-light)"/>
          <stop offset="1" stop-color="var(--smile-mid)"/>
        </linearGradient>
      </defs>
      <polygon fill="var(--green)" transform="translate(787 203)"
        points="29.5,-167.4 56.4,-88.6 139.3,-97.5 102.5,-22.7 167.4,29.5 88.6,56.4 97.5,139.3 22.7,102.5 -29.5,167.4 -56.4,88.6 -139.3,97.5 -102.5,22.7 -167.4,-29.5 -88.6,-56.4 -97.5,-139.3 -22.7,-102.5"/>
      <ellipse role="img" aria-label="Photo of a bright white smile" fill="url(#smileFill)"
        cx="820" cy="180" rx="132" ry="72" transform="rotate(12 820 180)"/>
      <path fill="var(--white)" transform="translate(641 83)" d="M0,-37 Q0,0 37,0 Q0,0 0,37 Q0,0 -37,0 Q0,0 0,-37 Z"/>
      <path fill="var(--white)" transform="translate(885 343)" d="M0,-31 Q0,0 31,0 Q0,0 0,31 Q0,0 -31,0 Q0,0 0,-31 Z"/>
      <path fill="var(--white)" transform="translate(846 396)" d="M0,-23 Q0,0 23,0 Q0,0 0,23 Q0,0 -23,0 Q0,0 0,-23 Z"/>
    </svg>

    <div class="brand-mark" aria-hidden="true"></div>
    <h1 class="brand-name">
      <span class="brand-name__primary">Harlow Brook</span>
      <span class="brand-name__secondary">Dentistry</span>
    </h1>
    <p class="website">Harlowbrookdentistry.example</p>
    <div class="phone-pill">
      <svg class="phone-icon" viewBox="0 0 38 62" aria-hidden="true">
        <path fill="var(--navy)" d="M30 2 C22 2 8 14 6 30 C4 46 14 60 22 60 L28 58 L24 44 L18 46 C14 40 15 24 20 17 L26 18 L32 4 Z"/>
      </svg>
      <span class="phone-number">(555) 847-1390</span>
    </div>
  </section>
</main>
</body>
</html>
```